Road Construction Company needs business cards

We would like a new business card designed for our business.

We're a road construction company based in Qld, Australia.

Can the business card please have the following information on it.

Name: Warren Halbeck
Position: General Manager
Phone: 0472 915 348
Email: Warren.halbeck@tovrin.com.au
Address: 87 Marrow Ave, Pendlebay, QLD, 4023
Website: www.tovrin.com.au

Visually we'd like the card to be professional and simple.

Attached is our logo.

Our website is www.tovrin.com.au

Target Market(s)

Men aged 25-60

Contact Information for Business Card

As listed in project description

Font styles to use
Serif

Requirements
Must have
• Large logo on back of card

```html
<!DOCTYPE html>
<html lang="en">
<head>
<meta charset="utf-8">
<title>Tovrin – Business Card</title>
<link href="https://fonts.googleapis.com/css2?family=Michroma&family=Exo+2:wght@400&display=swap" rel="stylesheet">
<style>
  :root {
    --page-bg: #e3e4e6;
    --card-bg: #ffffff;
    --brand-blue: #0b4f9f;
    --accent-blue: #2c9bd8;
    --ink: #1c1c1c;
    --shadow: rgba(0, 0, 0, 0.45);
  }
  html, body {
    margin: 0;
    padding: 0;
    width: 1200px;
    height: 900px;
    overflow: hidden;
    background: var(--page-bg);
  }
  .canvas {
    position: relative;
    width: 1200px;
    height: 900px;
  }
  .card {
    position: absolute;
    top: 217px;
    width: 308px;
    height: 499px;
    background: var(--card-bg);
    box-shadow: 2px 3px 3px var(--shadow);
  }
  .card--back {
    left: 279px;
    border-radius: 0 66px 0 66px;
  }
  .card--front {
    left: 617px;
    border-radius: 66px 0 66px 0;
  }
  .brand-name {
    position: absolute;
    margin: 0;
    font-family: "Michroma", sans-serif;
    font-weight: 400;
    font-size: 34px;
    letter-spacing: 2px;
    color: var(--brand-blue);
    line-height: 1;
    width: 100%;
    text-align: center;
  }
  .card--back .brand-name { top: 232px; }
  .card--front .brand-name { top: 152px; }

  .contact-block {
    position: absolute;
    left: 33px;
    top: 315px;
    font-family: "Exo 2", sans-serif;
    color: var(--ink);
  }
  .person-name {
    margin: 0;
    font-family: "Michroma", sans-serif;
    font-size: 14.5px;
    letter-spacing: 0.5px;
    color: var(--brand-blue);
    line-height: 18px;
  }
  .person-role {
    margin: 0 0 12px;
    font-size: 14px;
    color: var(--accent-blue);
    line-height: 18px;
  }
  .contact-list {
    list-style: none;
    margin: 0 0 10px;
    padding: 0;
  }
  .contact-item {
    display: flex;
    align-items: center;
    gap: 6px;
    font-size: 14px;
    line-height: 18px;
  }
  .contact-icon {
    width: 13px;
    height: 13px;
    fill: var(--brand-blue);
    flex: none;
  }
  .web-domain { color: var(--brand-blue); }
  .address {
    margin: 0;
    font-style: normal;
    font-size: 14px;
    line-height: 18px;
  }
</style>
</head>
<body>
<main class="canvas">
  <section class="card card--back" aria-label="Card back">
    <h1 class="brand-name">TOVRIN</h1>
  </section>

  <section class="card card--front" aria-label="Card front">
    <h2 class="brand-name">TOVRIN</h2>
    <div class="contact-block">
      <p class="person-name">WARREN HALBECK</p>
      <p class="person-role">General Manager</p>
      <ul class="contact-list">
        <li class="contact-item">
          <svg class="contact-icon" viewBox="0 0 24 24" aria-hidden="true"><path d="M6.6 10.8a15.2 15.2 0 0 0 6.6 6.6l2.2-2.2a1 1 0 0 1 1-.25 11.4 11.4 0 0 0 3.6.57 1 1 0 0 1 1 1V20a1 1 0 0 1-1 1A17 17 0 0 1 3 4a1 1 0 0 1 1-1h3.5a1 1 0 0 1 1 1c0 1.25.2 2.45.57 3.6a1 1 0 0 1-.25 1z"/></svg>
          <span>0472 915 348</span>
        </li>
        <li class="contact-item">
          <svg class="contact-icon" viewBox="0 0 24 24" aria-hidden="true"><path d="M2 5h20v14H2z M3.5 6.5 12 13l8.5-6.5" fill="var(--brand-blue)" stroke="#fff" stroke-width="1.5"/></svg>
          <span>Warren.halbeck@tovrin.com.au</span>
        </li>
        <li class="contact-item">
          <svg class="contact-icon" viewBox="0 0 24 24" aria-hidden="true" fill="none" stroke="var(--brand-blue)" stroke-width="2"><circle cx="12" cy="12" r="10"/><ellipse cx="12" cy="12" rx="4.5" ry="10"/><path d="M2 12h20M4 7h16M4 17h16"/></svg>
          <span>www.<span class="web-domain">tovrin</span>.com.au</span>
        </li>
      </ul>
      <address class="address">87 Marrow Ave<br>Pendlebay, QLD, 4023</address>
    </div>
  </section>
</main>
</body>
</html>
```